Telecommunications/Power civil contractor needs business card design

Were a new telecommunications/power underground civil contractor that is looking for a new business card design. Our company colours are silver or grey and orange. Feel free to use the white background logo or the black background logo.

Target Market(s)

Local contractors, utility companies, private sector mining/energy companies, developers.

Industry/Entity Type

Telecommunications

Contact Information for Business Card

Each card will need the following info:
Persons name:
Title:
E-mail:
Phone number:
Shop Address:
Mailing Address:

Requirements
Must have
• Each card will need the following info:
• Persons name:
• Title:
• E-mail:
• Phone number:
• Shop Address:
• Mailing Address:

```html
<!DOCTYPE html>
<html lang="en">
<head>
<meta charset="utf-8">
<title>Ridgeline Civil Works — Business Card</title>
<link rel="stylesheet" href="https://fonts.googleapis.com/css2?family=Source+Sans+3:wght@400;600;700&display=swap">
<style>
  :root {
    --backdrop-top: #4a4a4a;
    --backdrop-bottom: #2e2e2e;
    --card-white: #ffffff;
    --card-black: #060708;
    --orange: #f05a28;
    --grey: #6d6e71;
    --silver: #8a8b8d;
    --ink: #2b2b2b;
  }
  * { margin: 0; padding: 0; box-sizing: border-box; }
  html, body { width: 1200px; height: 900px; overflow: hidden; }
  body {
    background: linear-gradient(180deg, var(--backdrop-top), var(--backdrop-bottom));
    font-family: "Source Sans 3", "Myriad Pro", sans-serif;
    position: relative;
  }
  .card {
    position: absolute;
    top: 170px;
    width: 347px;
    height: 561px;
    overflow: hidden;
    box-shadow: 0 2px 6px rgba(0,0,0,0.35);
  }
  .card--front { left: 259px; background: var(--card-white); }
  .card--back { left: 631px; background: var(--card-black); }

  .band { position: absolute; left: 0; width: 347px; height: 32px; }
  .band--top { top: 0; }
  .band--bottom { bottom: 0; }

  .brand-mark { position: absolute; left: 0; width: 347px; }
  .brand-mark--front { top: 78px; height: 120px; }
  .brand-mark--back { top: 168px; height: 120px; }
  .brand-name {
    position: absolute; left: 0; width: 347px; text-align: center;
    font-weight: 700; letter-spacing: 0.04em; text-transform: uppercase;
  }
  .brand-name--front { top: 208px; font-size: 17px; color: var(--grey); }
  .brand-name--back { top: 334px; font-size: 27px; color: var(--orange); }

  .contact {
    position: absolute; top: 278px; left: 0; width: 347px;
    text-align: center; color: var(--ink);
  }
  .contact__name { font-size: 23px; font-weight: 600; letter-spacing: 0.01em; line-height: 1; }
  .contact__first { color: var(--orange); }
  .contact__last { color: var(--grey); }
  .contact__title { font-size: 15px; margin-top: 9px; }
  .contact__lines { font-size: 15px; line-height: 22px; margin-top: 18px; }
  .address { font-size: 15px; line-height: 17px; }
  .address--mailing { margin-top: 12px; }
  .address--shop { margin-top: 6px; }
  .address__label { color: var(--orange); font-weight: 600; }
</style>
</head>
<body>
  <section class="card card--front">
    <svg class="band band--top" viewBox="0 0 347 32" aria-hidden="true">
      <path d="M102 0 H246 V31 Q174 18 102 31 Z" fill="var(--orange)"/>
    </svg>

    <svg class="brand-mark brand-mark--front" viewBox="0 0 347 120" aria-hidden="true">
      <circle cx="173.5" cy="60" r="54" fill="none" stroke="var(--orange)" stroke-width="7"/>
    </svg>
    <div class="brand-name brand-name--front">Ridgeline Civil Works</div>

    <div class="contact">
      <div class="contact__name"><span class="contact__first">MARCUS</span> <span class="contact__last">HALE</span></div>
      <div class="contact__title">Managing Director</div>
      <div class="contact__lines">
        <div class="contact__phone">555-014-2368</div>
        <div class="contact__email">info@ridgelinecivil.com</div>
      </div>
      <div class="address address--mailing">
        <div class="address__label">Mailing Address</div>
        <div>1234, Address Goes Here</div>
        <div>Country Name, 123456</div>
      </div>
      <div class="address address--shop">
        <div class="address__label">Shop Address</div>
        <div>1234, Address Goes Here</div>
        <div>Country Name, 123456</div>
      </div>
    </div>

    <svg class="band band--bottom" viewBox="0 0 347 32" aria-hidden="true">
      <path d="M102 32 H246 V1 Q174 14 102 1 Z" fill="var(--orange)"/>
    </svg>
  </section>

  <section class="card card--back">
    <svg class="brand-mark brand-mark--back" viewBox="0 0 347 120" aria-hidden="true">
      <circle cx="173.5" cy="60" r="54" fill="none" stroke="var(--silver)" stroke-width="7"/>
    </svg>
    <div class="brand-name brand-name--back">Ridgeline Civil Works</div>
  </section>
</body>
</html>
```